Report template for evaluation reports to be used by non designers

We are looking for a report template that meets all the requirements listed in the attached documents. letter head, logo etc have been enclosed. Its important that the colour integrity is kept, but beyond that options are welcome.
Its important that the document is extremely easy to use and that is able to be adapted to include eatables, figures, pictures, text boxes etc and keep the integrity of the template

Target Market(s)

Governments, Civil society organisations and research institutions

Font styles to use
Sans Serif

Colors
6b449b
876aae
c0c0c0
000000

Requirements
Must have
• Clean, professional, not concluded, modern, must be easy to use
Should not have
• too busy, hard to use

```html
<!DOCTYPE html>
<html lang="en">
<head>
<meta charset="utf-8">
<title>Evaluation Report Template – Spread</title>
<link href="https://fonts.googleapis.com/css2?family=Open+Sans:wght@400;600;700&display=swap" rel="stylesheet">
<style>
  :root{
    --purple:#5a4a94;
    --purple-deep:#4a3c86;
    --purple-mid:#7f6fae;
    --purple-soft:#8a7bb8;
    --lilac:#e4e0ee;
    --silver:#c0c0c0;
    --ink:#000000;
    --text:#333333;
    --page:#f4f4f4;
    --backdrop:#a9a9a9;
  }
  *{box-sizing:border-box;margin:0;padding:0}
  html,body{width:1200px;height:912px;overflow:hidden}
  body{background:var(--backdrop);font-family:"Open Sans",Arial,sans-serif;color:var(--text);position:relative}
  .spread{position:absolute;left:20px;top:46px;width:1160px;height:820px;display:flex;box-shadow:0 8px 24px rgba(0,0,0,.25)}
  .page{position:relative;width:580px;height:820px;background:var(--page);overflow:hidden}
  .page--left{border-right:1px solid #dcdcdc}

  /* Chapter divider */
  .divider-panel{position:absolute;left:0;top:0}
  .divider-content{position:absolute;left:62px;top:84px;width:410px;color:#fff}
  .divider-title{font-size:27px;font-weight:700;margin-bottom:14px}
  .divider-text{font-size:11.5px;line-height:1.5}
  .brand-name{font-weight:600;color:var(--ink);letter-spacing:.04em;white-space:nowrap}
  .divider-brand{position:absolute;left:52px;bottom:70px;font-size:26px}

  /* Content page */
  .page-header{position:absolute;left:0;top:28px;width:580px;height:40px}
  .title-tab{position:absolute;left:0;top:12px;height:26px;background:linear-gradient(90deg,var(--purple-soft),var(--purple-mid));border-radius:0 12px 12px 0;color:#fff;font-size:11.5px;font-weight:700;line-height:26px;padding:0 20px 0 28px;white-space:nowrap}
  .title-rule{position:absolute;left:0;top:38px;width:580px;height:2px;background:var(--purple-mid)}
  .header-brand{position:absolute;right:50px;top:-14px;font-size:11px}
  .corner-tab{position:absolute;right:0;top:0;width:34px;height:26px;background:#555;border-radius:0 0 0 10px}

  .body{position:absolute;left:44px;top:86px;width:500px;font-size:9.5px;line-height:1.5}
  .body p{margin-bottom:14px}

  .data-table{border-collapse:separate;border-spacing:2px;font-size:8px;width:100%;margin-bottom:60px}
  .data-table th{background:var(--purple-mid);color:#fff;font-weight:700;padding:4px 4px;text-align:center}
  .data-table td{padding:4px 4px;text-align:center}
  .data-table tbody tr:nth-child(odd) td{background:var(--silver)}
  .data-table tbody tr:nth-child(even) td{background:var(--lilac)}
  .data-table .num{text-align:right}

  .tick-list{list-style:none;margin-top:-8px}
  .tick-list li{display:flex;align-items:center;gap:7px;margin-bottom:3px}
  .tick{width:10px;height:10px;flex:none}

  .page-footer{position:absolute;left:30px;bottom:36px;width:520px;height:58px}
  .page-pill{position:absolute;right:0;top:0;width:54px;height:18px;border-radius:9px;background:var(--purple-mid);color:#fff;font-size:8.5px;text-align:center;line-height:18px;font-weight:600}
  .footer-rule{position:absolute;left:0;top:8px;width:480px;height:2px;background:var(--purple-mid)}
  .footer-meta{position:absolute;left:0;top:16px;width:520px;display:flex;justify-content:space-between;font-size:8.5px;padding:0 66px 0 10px}
  .footer-bar{position:absolute;left:0;bottom:0;width:520px;height:18px;border:2px solid var(--purple-mid);border-radius:9px;font-size:8.5px;line-height:14px;padding:0 14px}
  .label{font-weight:700}
</style>
</head>
<body>
<div class="spread">
  <section class="page page--left" aria-label="Chapter divider page">
    <svg class="divider-panel" width="580" height="560" viewBox="0 0 580 560" aria-hidden="true">
      <defs>
        <linearGradient id="panelFill" x1="1" y1="0" x2="0" y2="1">
          <stop offset="0" stop-color="#8a7bb8"/>
          <stop offset=".45" stop-color="#5a4a94"/>
          <stop offset="1" stop-color="#4a3c86"/>
        </linearGradient>
      </defs>
      <path d="M24,0 H470 C515,0 535,30 535,80 V380 C535,445 505,470 440,480 L130,532 C62,542 24,505 24,440 Z" fill="url(#panelFill)"/>
    </svg>
    <div class="divider-content">
      <h1 class="divider-title">Chapter Divider</h1>
      <p class="divider-text">Lorem ipsum dolor sit amet, consectetur adipiscing elit. Fusce nisl metus, tempus sit amet auctor non, eleifend sit amet metus. Cras ante nibh, adipiscing in sodales at, semper at augue. Duis dictum posuere dolor, sed interdum massa laoreet id. Vivamus vehicula accumsan nibh, vel tincidunt nunc porta et. Praesent ligula tortor, luctus at laoreet eget, sagittis lacinia arcu. Duis laoreet nisl eget lectus sodales id mollis augue facilisis. Nam interdum purus sed ante tincidunt elementum facilisis non diam. Vestibulum tortor eros, laoreet sed malesuada quis, vel fermentum dui. Nunc et massa neque, at nec nunc. Aliquam lacinia malesuada laoreet. Nunc mollis, ligula ac volutpat venenatis, dui diam consequat quam, in tincidunt elit risus at dui.</p>
    </div>
    <div class="brand-name divider-brand">Meridian Research Institute</div>
  </section>

  <section class="page page--right" aria-label="Report content page">
    <header class="page-header">
      <div class="title-tab">Pre-Study for an Impact Evaluation of the ABC programme</div>
      <div class="title-rule"></div>
      <div class="brand-name header-brand">Meridian Research Institute</div>
    </header>
    <div class="corner-tab"></div>

    <div class="body">
      <p>Lorem ipsum dolor sit amet, consectetur adipiscing elit. Vestibulum vel ante ac ligula vestibulum hendrerit id eu mi. Vestibulum maximus mattis erat. Quisque lacus mi, volutpat vel justo eu, hendrerit blandit nibh. Nunc efficitur tincidunt sapien, in accumsan diam fringilla ut. Nullam molestie mi eget placerat rhoncus. Donec et pharetra enim. Nam fermentum nisl sit amet nulla posuere posuere. Quisque id arcu elementum, efficitur urna vel, tempor est.</p>

      <table class="data-table">
        <thead>
          <tr><th>No.</th><th>Lorium</th><th>Art. No.</th><th>haselius tincidunt</th><th>Quisque</th><th>ipsum</th></tr>
        </thead>
        <tbody>
          <tr><td>1</td><td>1</td><td>2331</td><td>consectetur adipiscing elit.</td><td class="num">7.450,00 €</td><td class="num">7.450,00 €</td></tr>
          <tr><td>2</td><td>0</td><td>5557</td><td>Praesent eleifend tempor velit</td><td class="num">5.490,00 €</td><td class="num">3.290,00 €</td></tr>
          <tr><td>3</td><td>1</td><td>9999</td><td>Quisque vitae tellus nisl</td><td class="num">365,00 €</td><td class="num">365,00 €</td></tr>
          <tr><td>4</td><td>2</td><td>7666</td><td>id tincidunt nunc turpis quis lacus</td><td class="num">6.490,00 €</td><td class="num">390,00 €</td></tr>
          <tr><td>5</td><td>1</td><td>194</td><td>Praesent tincidunt placerat felis</td><td class="num">5.490,00 €</td><td class="num">5.490,00 €</td></tr>
          <tr><td>6</td><td>3</td><td>540</td><td>Pellentesque ut nibh eget nisi cursus ultrices</td><td class="num">5.490,00 €</td><td class="num">5.490,00 €</td></tr>
          <tr><td>7</td><td>3</td><td>1945</td><td>Quisque id ipsum lorem</td><td class="num">5.490,00 €</td><td class="num">5.490,00 €</td></tr>
          <tr><td>8</td><td>2</td><td>5990</td><td>Duis rutrum scelerisque malesuada</td><td class="num"></td><td class="num"></td></tr>
        </tbody>
      </table>

      <p>Lorem ipsum dolor sit amet, consectetur adipiscing elit. Vestibulum vel ante ac ligula vestibulum hendrerit id eu mi. Vestibulum maximus mattis erat. Quisque lacus mi, volutpat vel justo eu, hendrerit blandit nibh:</p>
      <ul class="tick-list">
        <li><svg class="tick" viewBox="0 0 10 10" aria-hidden="true"><circle cx="5" cy="5" r="5" fill="#7f6fae"/><path d="M2.6 5.2 4.3 6.8 7.4 3.4" stroke="#fff" stroke-width="1.3" fill="none"/></svg>Vestibulum vel ante ac ligula vestibulum hendrerit id eu mi.</li>
        <li><svg class="tick" viewBox="0 0 10 10" aria-hidden="true"><circle cx="5" cy="5" r="5" fill="#7f6fae"/><path d="M2.6 5.2 4.3 6.8 7.4 3.4" stroke="#fff" stroke-width="1.3" fill="none"/></svg>Donec et pharetra enim. Nam fermentum nisl sit amet nulla posuere posuere.</li>
        <li><svg class="tick" viewBox="0 0 10 10" aria-hidden="true"><circle cx="5" cy="5" r="5" fill="#7f6fae"/><path d="M2.6 5.2 4.3 6.8 7.4 3.4" stroke="#fff" stroke-width="1.3" fill="none"/></svg>itae consequat lectus dignissim eget.</li>
      </ul>
    </div>

    <footer class="page-footer">
      <div class="footer-rule"></div>
      <div class="page-pill">2</div>
      <div class="footer-meta">
        <span></span>
        <span><span class="label">Client:</span> ABC Company</span>
        <span>September 22, 2018</span>
      </div>
      <div class="footer-bar"><span class="label">Report version:</span> 3</div>
    </footer>
  </section>
</div>
</body>
</html>
```